AUTO SPAREPART DISTRIBUTOR BUSINESS CARD

Our company need a business card design. We are a distributor and importer of car spareparts for VORN and PELTARO car model. We would like the design with White color back ground and attractive color for the fonts and looks clean, simple and attractive.
We provide the company information and the brand logo (VORN, PELTARO, ZUM, 738) should be put on the business card.

Thank you

Target Market(s)

Auto spareparts retailer shop and supplier.

Industry/Entity Type

Business

Contact Information for Business Card

The front side of the business card only contain company informations, and the back side may be put the brand logo (VORN, PELTARO, ZUM AND 738).

Requirements
Must have
• On the back side ( the brand logo) position , should have a transparency world map picture ( i uploaded the world map picture sample ).
• Also, need to put some words of " AUTO PARTS DISTRIBUTOR " (may be put on any appropriate place).

```html
<!DOCTYPE html>
<html lang="en">
<head>
<meta charset="utf-8">
<title>Norvata Inter Global – Business Card</title>
<link href="https://fonts.googleapis.com/css2?family=Open+Sans:wght@400;600&family=Roboto+Condensed:wght@700&display=swap" rel="stylesheet">
<style>
  :root {
    --stage: #000000;
    --card: #ffffff;
    --text: #333436;
    --green: #6aa33f;
    --lime: #86b83a;
    --divider: #dedfe0;
    --map: #c9cbce;
    --brand-blue: #1c4da0;
    --brand-red: #c8262c;
    --brand-grey: #6b6c6f;
  }
  * { margin: 0; padding: 0; box-sizing: border-box; }
  html, body { width: 1200px; height: 900px; overflow: hidden; background: var(--stage); }
  body { position: relative; font-family: "Open Sans", sans-serif; color: var(--text); }

  .card {
    position: absolute; top: 271px; width: 457px; height: 281px;
    background: var(--card); border-radius: 14px; overflow: hidden;
  }
  .card--front { left: 137px; }
  .card--back { left: 626px; }

  /* front */
  .mark {
    position: absolute; left: 36px; top: 105px; width: 110px;
    display: flex; flex-direction: column; align-items: center; gap: 12px;
  }
  .mark__square { width: 52px; height: 52px; background: var(--green); }
  .mark__name { font-size: 15px; font-weight: 600; color: var(--lime); letter-spacing: 1px; }

  .divider {
    position: absolute; left: 177px; top: 78px; width: 1px; height: 112px;
    background: var(--divider);
  }
  .details { position: absolute; left: 204px; top: 42px; }
  .person__name { font-size: 14.5px; font-weight: 600; color: var(--green); line-height: 18px; }
  .person__role { font-size: 12.5px; line-height: 16px; }
  .address { margin-top: 15px; font-size: 12.5px; line-height: 16.3px; }
  .contacts { margin-top: 13px; list-style: none; }
  .contacts li { display: flex; align-items: center; font-size: 12.5px; line-height: 16.4px; white-space: nowrap; }
  .contacts svg { width: 10px; height: 10px; margin-left: 1px; margin-right: 6px; fill: var(--green); flex: none; }

  /* back */
  .world-map {
    position: absolute; left: 30px; top: 168px; width: 397px; height: 100px;
    background: radial-gradient(ellipse at center, var(--map) 0%, rgba(201,203,206,0.35) 55%, rgba(201,203,206,0) 75%);
    opacity: 0.6;
  }
  .company {
    position: absolute; left: 92px; top: 76px;
    display: flex; align-items: center; gap: 12px;
  }
  .company__square { width: 38px; height: 38px; background: var(--green); flex: none; }
  .company__name {
    font-family: "Roboto Condensed", sans-serif; font-weight: 700;
    font-size: 27px; letter-spacing: -0.6px; white-space: nowrap; color: var(--text);
  }
  .tagline {
    position: absolute; left: 142px; top: 126px;
    font-size: 10px; font-weight: 600; letter-spacing: 2.4px; color: var(--green); white-space: nowrap;
  }
  .brands {
    position: absolute; left: 79px; top: 214px; width: 290px;
    display: flex; justify-content: space-between; align-items: center;
    font-size: 12px; font-weight: 600; letter-spacing: 0.5px;
  }
  .brand--peltaro { color: var(--brand-blue); }
  .brand--vorn { color: var(--brand-red); }
  .brand--zum { color: var(--brand-grey); font-size: 17px; font-weight: 400; }
  .brand--738 { color: var(--brand-red); }
</style>
</head>
<body>

<section class="card card--front">
  <div class="mark">
    <div class="mark__square"></div>
    <div class="mark__name">NORVATA</div>
  </div>
  <div class="divider"></div>
  <div class="details">
    <p class="person__name">RAFI TANOTO</p>
    <p class="person__role">Director</p>
    <p class="address">Taman Arcadia 4 , Blok c-07 No.B-09 ,<br>Kalideres, Jakarta Barat,<br>Indonesia (11840).</p>
    <ul class="contacts">
      <li><svg viewBox="0 0 10 10"><path d="M2 0.5 3.6 2.6 2.7 3.7C3.3 5 4.6 6.4 6 7.1L7.1 6.2 9.4 7.8 8.4 9.5C4.4 9.3 0.6 5.5 0.4 1.6Z"/></svg>+62-21-50017342</li>
      <li><svg viewBox="0 0 10 10"><rect x="0.5" y="3.5" width="9" height="6" rx="1"/><rect x="2.5" y="0.5" width="5" height="3"/></svg>+62-21-50017348</li>
      <li><svg viewBox="0 0 10 10"><path d="M2.5 0h5v10h-5zM3.5 1v7h3V1z" fill-rule="evenodd"/></svg>+62-811904275</li>
      <li><svg viewBox="0 0 10 10"><path d="M0.5 2h9v6.5h-9zM1.5 3 5 5.8 8.5 3z" fill-rule="evenodd"/></svg>norvata-indonesia@mailbox.com</li>
      <li><svg viewBox="0 0 10 10"><circle cx="5" cy="5" r="4.6"/></svg>rafi.tan27</li>
    </ul>
  </div>
</section>

<section class="card card--back">
  <div class="world-map" role="img" aria-label="Faint transparent world map behind the brand names"></div>
  <div class="company">
    <div class="company__square"></div>
    <h1 class="company__name">PT.NORVATA INTER GLOBAL</h1>
  </div>
  <p class="tagline">AUTO PARTS DISTRIBUTOR</p>
  <div class="brands">
    <span class="brand--peltaro">PELTARO</span>
    <span class="brand--vorn">VORN</span>
    <span class="brand--zum">ZUM</span>
    <span class="brand--738">738</span>
  </div>
</section>

</body>
</html>
```